Dental Medical History Form - Content provided

Design a medical history form for a dental practice. Content is provided so all that is needed is the formatting to make it look great and easy to read.

"Patient Information" to include all information contained in top portion of the "Patient Medical History Form" docx file.

"Medical History" should follow the formatting and content of the "Exact Medical History" file as this is what the entry fields look like in our practice software and so we would like it to match.

1st page - Patient info, allergies, medications, antibiotics, joint replacement, pregnancy.

2nd page - Do you have, or have you had, any of the following? . . . . . . .
Updates

Target Market(s)

All ages but must be clear enough for elderly to read. Use as much space as possible to keep font size bigger yet keep to two pages

Industry/Entity Type

Dental

Font styles to use
Sans Serif

Requirements
Must have
• All content provided
• Our logo at the top (file provided)
• Century Gothic Font
• Limit to two pages

```html
<!DOCTYPE html>
<html lang="en">
<head>
<meta charset="utf-8">
<title>Keystone Dental – Confidential Medical History</title>
<link rel="stylesheet" href="https://fonts.googleapis.com/css2?family=PT+Sans+Narrow:wght@400;700&display=swap">
<style>
  :root{
    --bg:#e4e4e6;
    --paper:#ffffff;
    --ink:#3b404b;
    --navy:#2e3669;
    --rule:#6d717c;
    --band-dark:#b9babf;
    --band-light:#f4f4f5;
  }
  *{box-sizing:border-box;margin:0;padding:0}
  html,body{width:1200px;height:784px;overflow:hidden;background:var(--bg)}
  body{font-family:"PT Sans Narrow",sans-serif;color:var(--ink);font-size:10px;position:relative}
  .page{position:absolute;left:325px;top:8px;width:550px;height:768px;background:var(--paper);
        box-shadow:0 2px 6px rgba(0,0,0,.12);padding:20px 30px 0 30px}
  .edge-tab{position:absolute;top:34px;width:34px;height:14px;background:linear-gradient(180deg,var(--band-dark),var(--band-light))}
  .edge-tab.left{left:0;clip-path:polygon(0 0,80% 0,100% 100%,0 100%)}
  .edge-tab.right{right:0;clip-path:polygon(20% 0,100% 0,100% 100%,0 100%)}

  .masthead{display:flex;justify-content:space-between;align-items:flex-start;height:74px}
  .brand{display:flex;flex-direction:column;align-items:flex-start;padding-left:60px}
  .brand-name{display:flex;align-items:center;gap:6px;font-size:30px;color:var(--rule);line-height:1;letter-spacing:.5px}
  .brand-name .mark{width:9px;height:9px;background:var(--rule)}
  .doc-title{margin-top:8px;font-weight:700;font-size:13px;letter-spacing:3px;color:var(--ink);
             text-decoration:underline;text-underline-offset:3px}
  .contact{text-align:right;font-weight:700;font-size:9px;line-height:1.25;color:var(--ink);padding-top:12px}
  .contact .phone{font-size:11px}

  .row{display:flex;align-items:center;gap:6px;height:19px;white-space:nowrap}
  .label{flex:none}
  .field{flex:1;height:14px;border:1px solid var(--rule)}
  .field.w-s{flex:0 0 70px}.field.w-m{flex:0 0 110px}
  .name-captions{display:flex;height:12px;padding-left:48px;font-size:9px}
  .name-captions span{flex:1;padding-left:55px}
  .check{display:inline-block;width:9px;height:9px;border:1px solid var(--rule);vertical-align:middle;margin:0 4px 0 2px}
  .options{display:flex;justify-content:space-between;height:19px;align-items:center}

  .band{position:relative;margin:6px -30px 4px;height:22px;border-bottom:1px solid var(--navy);
        background:linear-gradient(180deg,var(--band-light),var(--band-dark) 55%,var(--band-light));
        text-align:center;font-weight:700;font-size:10px;line-height:22px;color:var(--ink)}
  .write-line{height:20px;border-bottom:1px solid var(--rule)}
  .questions{margin-top:14px}
  .questions .row{height:18px}
  .q-text{width:150px}

  .footer{position:absolute;left:0;right:0;bottom:0;height:18px;
          background:linear-gradient(180deg,var(--band-light),var(--band-dark))}
  .turnover{position:absolute;left:40px;bottom:18px;padding:2px 16px;font-weight:700;font-size:10px;
            background:linear-gradient(180deg,var(--band-light),var(--band-dark));border-radius:4px 4px 0 0}
</style>
</head>
<body>
<main class="page">
  <span class="edge-tab left"></span><span class="edge-tab right"></span>

  <header class="masthead">
    <div class="brand">
      <div class="brand-name"><span>keystone dental</span><span class="mark"></span></div>
      <h1 class="doc-title">CONFIDENTIAL MEDICAL HISTORY</h1>
    </div>
    <address class="contact">
      <div class="phone">(02) 4000 1234</div>
      Keystone Dental, Suite 4, 18 Harbour Rd<br>Westbay NSW 2000
    </address>
  </header>

  <section class="patient">
    <div class="name-captions"><span>First</span><span>Middle</span><span>Last</span></div>
    <div class="row"><span class="label">Name:</span><span class="field"></span><span class="field"></span><span class="field"></span></div>
    <div class="row"><span class="label">Address:</span><span class="field"></span><span class="label">Email Address:</span><span class="field"></span></div>
    <div class="row"><span class="label">DOB:</span><span class="field w-s"></span><span class="label">Phone Number(s): Mobile</span><span class="field"></span><span class="label">Work</span><span class="field"></span><span class="label">Home</span><span class="field"></span></div>
    <div class="row"><span class="label">Emergency Contact Person: Name:</span><span class="field"></span><span class="label">Relationship:</span><span class="field w-s"></span><span class="label">Phone number:</span><span class="field"></span></div>
  </section>

  <div class="band">General Practitioner:</div>
  <section class="gp">
    <div class="row"><span class="label">Name:</span><span class="field"></span><span class="label">Phone Number:</span><span class="field"></span></div>
    <div class="row"><span class="label">Practice Name:</span><span class="field"></span><span class="label">Referred by:</span><span class="field"></span></div>
    <div class="row"><span class="label">Do you have a health fund with dental cover? Yes<span class="check"></span>or No<span class="check"></span> If so, what is the name of the fund?</span><span class="field"></span></div>
    <div class="row"><span class="label">Fund Number:</span><span class="field"></span><span class="label">Priority Number on card: 0<span class="check"></span>1<span class="check"></span>2<span class="check"></span>3<span class="check"></span>4<span class="check"></span>5<span class="check"></span></span></div>
    <div class="row"><span class="label">Occupation:</span><span class="field"></span></div>
  </section>

  <div class="band">Please indicate if you are allergic to any of the following:</div>
  <section class="allergies">
    <div class="options"><span>Aspirin<span class="check"></span></span><span>Codeine<span class="check"></span></span><span>Penicillin<span class="check"></span></span><span>Sulfites<span class="check"></span></span><span>Latex<span class="check"></span></span><span>Local Anaesthetic<span class="check"></span></span><span>Lactose<span class="check"></span></span><span>Nickel<span class="check"></span></span></div>
    <div class="row"><span class="label">Other:</span><span class="field"></span></div>
  </section>

  <div class="band">Are you currently taking, or have ever taken, any of the following medication?</div>
  <section class="medications">
    <div class="options"><span>Asthma inhaler<span class="check"></span></span><span>Anti-epileptics<span class="check"></span></span><span>Anti-depressants<span class="check"></span></span><span>Blood Pressure<span class="check"></span></span><span>Blood Thinners<span class="check"></span></span><span>Bisphosphonates<span class="check"></span></span></div>
    <div class="options"><span>Chemotherapy<span class="check"></span></span><span>Insulin<span class="check"></span></span><span>Immunosuppressants<span class="check"></span></span><span>Steroids<span class="check"></span></span><span>Oral Contraceptive<span class="check"></span></span><span>Other<span class="check"></span></span></div>
  </section>

  <div class="band">Please specify medication name, dose, and frequency where possible:</div>
  <section class="medication-notes">
    <div class="write-line"></div><div class="write-line"></div><div class="write-line"></div>
  </section>

  <section class="questions">
    <div class="row"><span class="q-text">Do you require antibiotic cover?</span>Yes<span class="check"></span>No<span class="check"></span></div>
    <div class="row"><span class="q-text">Have you had a joint replacement?</span>Yes<span class="check"></span>No<span class="check"></span></div>
    <div class="row"><span class="q-text">Women: &nbsp;Are you pregnant?</span>Yes<span class="check"></span>No<span class="check"></span>Possible<span class="check"></span>&nbsp; or &nbsp;Breast Feeding? &nbsp;Yes<span class="check"></span>No<span class="check"></span></div>
  </section>

  <div class="turnover">Please Turnover</div>
  <div class="footer"></div>
</main>
</body>
</html>
```